KAJU Freightways #ALLKAJU Business Cards & Letterhead

I am looking to business cards designed for our organization. We are currently undergoing a small re-branding that is taking place. Our organization is called KAJU Freightways and we are headquartered in Phoenix, AZ. We primarily provide transportation and logistics services to the Marlow Parcel Bureau who is our largest customer. I would like to see a design that incorporates name, title, contact info, website, and address (this will be different depending on the employee). I would also like to see some color on the business card using our logo colors or a variation. I would like our logo on the back of the business card with the website displayed. The final design should communicate that we are a next generation transportation operate that focuses on being driver-first, customer-centric, innovative, and sustainable.We would also like our #ALLKAJU catch phrase incorporated as well.

Target Market(s)

Transportation & Logistics

Industry/Entity Type

Trucking Company

Contact Information for Business Card

-First and Last Name
-Position Title
-Contact Phone
-Contact Email
-Physical Address

Font styles to use
Serif

Colors

Designer to choose colors to be used in the design.

Requirements
Must have
• -KAJU logo prominently displayed
• -#ALLKAJU catch phrase used
• -Some amount of color, design gradient, etc.
• -Logo on the back with website listed (https://www.kajufreightco.example)

```html
<!DOCTYPE html>
<html lang="en">
<head>
<meta charset="utf-8">
<title>KAJU Freightways – Letterhead &amp; Business Cards</title>
<link href="https://fonts.googleapis.com/css2?family=Lato:wght@400;700;900&family=Arimo:wght@400;700&display=swap" rel="stylesheet">
<style>
  :root {
    --navy: #163844;
    --green: #7bbd42;
    --paper: #f5f5f5;
    --ink: #1c1c1c;
    --white: #ffffff;
    --backdrop-light: #ececec;
    --backdrop-dark: #dcdcdc;
  }
  * { margin: 0; padding: 0; box-sizing: border-box; }
  html, body { width: 1200px; height: 1200px; overflow: hidden; }
  body {
    background: radial-gradient(circle at 50% 50%, var(--backdrop-light), var(--backdrop-dark));
    font-family: "Lato", sans-serif;
  }
  .stage {
    position: absolute; left: 0; top: 0;
    width: 1932px; height: 1932px;
    transform: scale(0.62112); transform-origin: 0 0;
  }
  .sheet {
    position: absolute; overflow: hidden;
    background: var(--paper);
    box-shadow: 3px 4px 8px rgba(0,0,0,.28);
  }
  .sheet > svg.art { position: absolute; left: 0; top: 0; }

  /* Letterhead */
  .letterhead { left: 138px; top: 249px; width: 1132px; height: 1463px; }
  .brand-mark {
    position: absolute; display: flex; align-items: center; justify-content: center;
    border-radius: 50%; background: var(--white);
    border: 6px solid var(--green);
    font-family: "Lato", sans-serif; font-weight: 900; color: var(--navy);
  }
  .letterhead .brand-mark { left: 86px; top: 62px; width: 140px; height: 140px; font-size: 38px; }
  .divider { position: absolute; width: 3px; background: var(--navy); }
  .letterhead .divider { left: 250px; top: 88px; height: 90px; }
  .tagline { position: absolute; color: var(--green); font-weight: 400; }
  .letterhead .tagline { left: 276px; top: 100px; font-size: 26px; line-height: 30px; }
  .contact-block {
    position: absolute; right: 62px; top: 40px; text-align: right;
    color: var(--white); font-size: 16.5px; line-height: 20px;
  }
  .contact-block .company { font-weight: 700; }
  .contact-block .gap { height: 10px; }
  .contact-line { display: flex; justify-content: flex-end; align-items: center; gap: 5px; }
  .icon { width: 13px; height: 13px; flex: none; }

  .letter {
    position: absolute; left: 88px; top: 372px; width: 970px;
    font-family: "Arimo", sans-serif; color: var(--ink);
    font-size: 16px; line-height: 22.3px;
  }
  .letter p { margin-bottom: 22px; text-align: justify; }
  .letter .date { margin-bottom: 22px; }
  .letter .recipient { margin-bottom: 44px; text-align: left; }
  .letter .salutation { font-weight: 700; margin-bottom: 44px; }
  .letter .closing { margin-top: 58px; margin-bottom: 18px; }
  .signature {
    width: 230px; height: 36px; margin-bottom: 22px;
    background: linear-gradient(90deg, rgba(30,30,30,.18), rgba(30,30,30,.05));
    border-radius: 4px;
  }
  .signer { text-align: left; }
  .hashtag { position: absolute; color: var(--white); font-weight: 400; }
  .hashtag span { color: var(--green); }
  .letterhead .hashtag { left: 935px; top: 1395px; font-size: 20px; }

  /* Business cards */
  .card { left: 1351px; width: 466px; height: 266px; }
  .card-back { top: 455px; background: var(--navy); }
  .card-back .brand-mark { left: 98px; top: 88px; width: 90px; height: 90px; font-size: 24px; background: var(--navy); color: var(--white); border-width: 4px; }
  .card-back .divider { left: 205px; top: 85px; height: 95px; width: 2px; background: var(--white); }
  .card-back .tagline { left: 222px; top: 113px; font-size: 16px; line-height: 20px; }
  .card-back .web { position: absolute; left: 0; right: 0; top: 222px; text-align: center; color: var(--white); font-size: 12px; letter-spacing: 1.6px; }
  .card-back .web span { color: var(--green); }

  .card-front { top: 761px; }
  .card-front .brand-mark { left: 30px; top: 24px; width: 94px; height: 94px; font-size: 25px; border-width: 4px; }
  .card-front .person { position: absolute; right: 34px; top: 32px; text-align: right; }
  .card-front .name { color: var(--green); font-weight: 700; font-size: 16.5px; }
  .card-front .title { color: var(--white); font-size: 12px; }
  .card-front .details { position: absolute; left: 32px; top: 130px; color: var(--navy); font-size: 12px; line-height: 15.7px; }
  .card-front .details .company { font-weight: 700; }
  .card-front .details .gap { height: 6px; }
  .card-front .contact-line { justify-content: flex-start; gap: 4px; }
  .card-front .icon { width: 10px; height: 10px; }
  .card-front .details .accent { color: var(--green); }
  .card-front .hashtag { left: 366px; top: 236px; font-size: 13px; }
</style>
</head>
<body>
<div class="stage">

  <!-- Letterhead -->
  <section class="sheet letterhead">
    <svg class="art" width="1132" height="1463" viewBox="0 0 1132 1463" aria-hidden="true">
      <path fill="var(--green)" d="M0,0 H1132 V235 C1000,250 900,235 700,175 C520,115 420,62 300,78 C180,95 80,150 0,222 Z"/>
      <path fill="var(--navy)" d="M0,0 H1132 V180 C1000,215 900,205 700,140 C520,80 420,50 300,75 C180,100 80,150 0,215 Z"/>
      <path fill="var(--green)" d="M228,1463 C520,1375 860,1330 1132,1360 V1463 Z"/>
      <path fill="var(--navy)" d="M430,1463 C660,1398 900,1362 1132,1367 V1463 Z"/>
    </svg>
    <div class="brand-mark">KAJU</div>
    <div class="divider"></div>
    <div class="tagline">Transportation<br>and Energy Services</div>
    <div class="contact-block">
      <div class="company">KAJU Freightways &amp; Energy Services, Inc.</div>
      <div>4410 North Canyon Ridge Road</div>
      <div>Phoenix, AZ 85021</div>
      <div class="gap"></div>
      <div class="contact-line">602-555-0148
        <svg class="icon" viewBox="0 0 16 16"><path fill="var(--green)" d="M3.5 1 6 3.5 4.6 5.6c.9 2 2.4 3.5 4.4 4.4L11 8.6 15 11l-1 3c-6.5.6-12.6-5.5-12-12z"/></svg></div>
      <div class="contact-line">info@kajufreightco.example
        <svg class="icon" viewBox="0 0 16 16"><rect x="1" y="3" width="14" height="10" fill="none" stroke="var(--green)" stroke-width="1.6"/><path d="M1 3 8 9 15 3" fill="none" stroke="var(--green)" stroke-width="1.6"/></svg></div>
      <div class="contact-line">www.kajufreightco.example
        <svg class="icon" viewBox="0 0 16 16"><circle cx="8" cy="8" r="6.5" fill="none" stroke="var(--green)" stroke-width="1.5"/><path d="M1.5 8h13M8 1.5c-3 3.5-3 9.5 0 13M8 1.5c3 3.5 3 9.5 0 13" fill="none" stroke="var(--green)" stroke-width="1.2"/></svg></div>
    </div>

    <article class="letter">
      <div class="date">November 15, 2019</div>
      <div class="recipient">Mr. John Doe<br>President<br>AA Corporation<br>111 Street Name, Suite#<br>City, State, 12345</div>
      <div class="salutation">Dear Mr. John,</div>
      <p>Lorem ipsum dolor sit amet, consectetur adipiscing elit. Integer diam quam, egestas eu ultrices eu, suscipit ac sapien. Phasellus eu dui nisi. Nam et euismod diam, nec lobortis tortor. Donec et diam nulla. Aenean varius tincidunt convallis. Aliquam a tortor at lacus dictum aliquet. Nunc laoreet metus sapien, in scelerisque augue consectetur in.</p>
      <p>Fusce nec justo laoreet, egestas justo sed, aliquet sem. Pellentesque pharetra massa non orci bibendum semper. Pellentesque cursus eu lectus a consectetur. Nunc volutpat suscipit posuere. Vestibulum facilisis vel quam malesuada mattis. Nulla in mattis tellus. Maecenas tristique mauris vitae pharetra tincidunt. In ut ornare risus. Integer molestie vestibulum nisi, semper dapibus mi condimentum eu.</p>
      <p>Nullam sagittis elit libero, id fringilla est tincidunt eget. Donec in ipsum ultricies, consectetur quam vel, facilisis elit. Phasellus tincidunt congue risus vel luctus. Suspendisse ut mollis neque. Donec ornare orci in turpis vestibulum, in ultrices metus scelerisque. Pellentesque mattis mattis nunc, nec tincidunt lacus egestas id. Fusce facilisis sagittis neque sit amet vulputate. Aliquam ut eros lobortis tortor facilisis vehicula. Sed sed luctus leo, at laoreet sapien. Donec placerat adipiscing ligula non euismod. In lobortis pretium nisl id luctus.</p>
      <p>Integer gravida tincidunt nibh, scelerisque tincidunt turpis. Suspendisse potenti. Nunc hendrerit euismod lectus id elementum. Fusce vitae gravida velit, quis eleifend lectus. In imperdiet mauris eu dui viverra sagittis. Donec tempor dui diam, condimentum gravida lacus pretium a. Nullam fringilla augue quis arcu placerat scelerisque. Aliquam nec tincidunt augue, sit amet posuere ipsum.</p>
      <div class="closing">Sincerely Yours,</div>
      <div class="signature" role="img" aria-label="Handwritten signature of Rowan Delacroix"></div>
      <div class="signer">Rowan Delacroix<br>President</div>
    </article>

    <div class="hashtag"><span>#</span>ALLKAJU</div>
  </section>

  <!-- Business card back -->
  <section class="sheet card card-back">
    <div class="brand-mark">KAJU</div>
    <div class="divider"></div>
    <div class="tagline">Transportation<br>and Energy Services</div>
    <div class="web">www.<span>kajufreightco</span>.example</div>
  </section>

  <!-- Business card front -->
  <section class="sheet card card-front">
    <svg class="art" width="466" height="266" viewBox="0 0 466 266" aria-hidden="true">
      <path fill="var(--green)" d="M0,0 H466 V112 C390,122 330,105 250,75 C180,50 120,38 70,45 C40,50 18,70 0,92 Z"/>
      <path fill="var(--navy)" d="M0,0 H466 V86 C390,102 330,90 250,62 C180,40 120,30 70,38 C40,44 18,66 0,88 Z"/>
      <path fill="var(--green)" d="M140,266 C240,230 360,205 466,222 V266 Z"/>
      <path fill="var(--navy)" d="M200,266 C290,238 380,222 466,226 V266 Z"/>
    </svg>
    <div class="brand-mark">KAJU</div>
    <div class="person">
      <div class="name">ROWAN DELACROIX</div>
      <div class="title">President</div>
    </div>
    <div class="details">
      <div class="company">KAJU Freightways &amp; Energy Services, Inc.</div>
      <div>4410 North Canyon Ridge Road</div>
      <div>Phoenix, AZ 85021</div>
      <div class="gap"></div>
      <div class="contact-line">
        <svg class="icon" viewBox="0 0 16 16"><path fill="var(--green)" d="M3.5 1 6 3.5 4.6 5.6c.9 2 2.4 3.5 4.4 4.4L11 8.6 15 11l-1 3c-6.5.6-12.6-5.5-12-12z"/></svg>602-555-0148</div>
      <div class="contact-line">
        <svg class="icon" viewBox="0 0 16 16"><rect x="1" y="3" width="14" height="10" fill="none" stroke="var(--green)" stroke-width="1.8"/><path d="M1 3 8 9 15 3" fill="none" stroke="var(--green)" stroke-width="1.8"/></svg>rowan@kajufreightco.example</div>
      <div class="contact-line">
        <svg class="icon" viewBox="0 0 16 16"><circle cx="8" cy="8" r="6.5" fill="none" stroke="var(--green)" stroke-width="1.6"/><path d="M1.5 8h13M8 1.5c-3 3.5-3 9.5 0 13M8 1.5c3 3.5 3 9.5 0 13" fill="none" stroke="var(--green)" stroke-width="1.3"/></svg>www.<span class="accent">kajufreightco</span>.example</div>
    </div>
    <div class="hashtag"><span>#</span>ALLKAJU</div>
  </section>

</div>
</body>
</html>
```